AUTO SPAREPART DISTRIBUTOR BUSINESS CARD

Our company need a business card design. We are a distributor and importer of car spareparts for VORN and PELTARO car model. We would like the design with White color back ground and attractive color for the fonts and looks clean, simple and attractive.
We provide the company information and the brand logo (VORN, PELTARO, ZUM, 738) should be put on the business card.

Thank you

Target Market(s)

Auto spareparts retailer shop and supplier.

Industry/Entity Type

Business

Contact Information for Business Card

The front side of the business card only contain company informations, and the back side may be put the brand logo (VORN, PELTARO, ZUM AND 738).

Requirements
Must have
• On the back side ( the brand logo) position , should have a transparency world map picture ( i uploaded the world map picture sample ).
• Also, need to put some words of " AUTO PARTS DISTRIBUTOR " (may be put on any appropriate place).

```html
<!DOCTYPE html>
<html lang="en">
<head>
<meta charset="utf-8">
<title>ZUM Auto Parts Distributor – Business Card</title>
<link rel="stylesheet" href="https://fonts.googleapis.com/css2?family=Raleway:wght@200&family=Roboto:wght@400;700&display=swap">
<style>
  :root {
    --bg: #ecebe7;
    --card-white: #f7f7f7;
    --card-shade: #e2e2e2;
    --green-dark: #52a52c;
    --green-light: #a4d257;
    --green-text: #7fbf3f;
    --ink: #1c1c1c;
    --grey: #8a8a8a;
    --map: #a9a9a9;
    --white: #ffffff;
    --brand-blue: #1b3f91;
    --brand-red: #d42a25;
  }
  * { margin: 0; padding: 0; box-sizing: border-box; }
  html, body { width: 1200px; height: 1023px; overflow: hidden; background: var(--bg); }
  body { position: relative; font-family: 'Roboto', Arial, sans-serif; }

  .card {
    position: absolute;
    width: 600px; height: 345px;
    border-radius: 18px;
    overflow: hidden;
    box-shadow: 0 6px 18px rgba(0,0,0,.18);
  }

  /* Front */
  .card-front {
    left: 70px; top: 90px;
    background: linear-gradient(160deg, var(--white) 0%, var(--card-white) 55%, var(--card-shade) 100%);
  }
  .world-map {
    position: absolute; right: 40px; top: 36px;
    width: 300px; height: 150px;
    border-radius: 40px 60px 30px 70px;
    background: radial-gradient(ellipse at 50% 45%, var(--map) 0%, rgba(169,169,169,.55) 55%, rgba(169,169,169,0) 80%);
  }
  .brand-lockup {
    position: absolute; left: 48px; top: 170px;
    display: flex; align-items: center; gap: 22px;
  }
  .brand-square { width: 58px; height: 58px; background: var(--green-dark); }
  .brand-name {
    font-family: 'Raleway', Arial, sans-serif;
    font-weight: 200; font-size: 110px; line-height: 1;
    letter-spacing: 6px; color: var(--ink);
  }
  .tagline {
    position: absolute; left: 210px; top: 290px;
    font-size: 17px; letter-spacing: .5px; color: var(--green-text);
  }

  /* Back */
  .card-back {
    left: 530px; top: 580px;
    background: linear-gradient(135deg, var(--green-dark) 0%, var(--green-light) 70%, var(--green-dark) 100%);
    color: var(--white);
  }
  .name-pill {
    position: absolute; right: 0; top: 34px;
    width: 330px; height: 64px;
    background: var(--white);
    border-radius: 32px 0 0 32px;
    padding: 9px 0 0 30px;
  }
  .person-name { font-size: 24px; color: var(--green-text); letter-spacing: .5px; }
  .person-title { font-size: 14px; color: #444; margin-top: 2px; }
  .address {
    position: absolute; left: 30px; top: 112px;
    font-size: 14px; line-height: 1.4; width: 430px;
  }
  .contact-list {
    position: absolute; left: 30px; top: 168px;
    list-style: none; font-size: 13.5px; line-height: 1.55;
  }
  .contact-list li { display: flex; align-items: center; gap: 8px; }
  .contact-list svg { width: 12px; height: 12px; fill: none; stroke: var(--white); stroke-width: 1.4; }
  .partner-brands {
    position: absolute; left: 30px; bottom: 22px;
    display: flex; align-items: baseline; gap: 30px;
    font-weight: 700; font-size: 18px;
  }
  .partner-peltaro { color: var(--brand-blue); }
  .partner-vorn { color: var(--brand-red); }
  .partner-738 { color: var(--brand-red); }
  .partner-note { font-size: 7px; font-weight: 400; color: #2f5d1a; }
  .back-watermark {
    position: absolute; right: 26px; bottom: 14px;
    font-family: 'Raleway', Arial, sans-serif; font-weight: 200;
    font-size: 72px; color: rgba(255,255,255,.28); letter-spacing: 4px;
  }
</style>
</head>
<body>
  <section class="card card-front">
    <div class="world-map" role="img" aria-label="Transparent grey world map"></div>
    <div class="brand-lockup">
      <span class="brand-square"></span>
      <span class="brand-name">ZUM</span>
    </div>
    <p class="tagline">AUTO PARTS DISTRIBUTOR</p>
  </section>

  <section class="card card-back">
    <div class="name-pill">
      <p class="person-name">RENO TAMARA</p>
      <p class="person-title">Director</p>
    </div>
    <p class="address">Taman Seroja 4, Blok C-07 No.B-9,<br>Kalideres Utara, Jakarta Barat, Indonesia (11840)</p>
    <ul class="contact-list">
      <li><svg viewBox="0 0 12 12"><path d="M2 1.5l2 0 1 2.5-1.2 1a6 6 0 0 0 3.2 3.2l1-1.2 2.5 1v2a1 1 0 0 1-1 1A9 9 0 0 1 1 2.5a1 1 0 0 1 1-1z"/></svg>+62-21-58307412</li>
      <li><svg viewBox="0 0 12 12"><rect x="3" y="1" width="6" height="10" rx="1"/><path d="M5.5 9h1"/></svg>+62-817450936</li>
      <li><svg viewBox="0 0 12 12"><rect x="1.5" y="4" width="9" height="6"/><path d="M3.5 4V1.5h5V4M3.5 7h5"/></svg>+62-21-58307419</li>
      <li><svg viewBox="0 0 12 12"><rect x="1" y="2.5" width="10" height="7"/><path d="M1 2.5l5 4 5-4"/></svg>zum-parts@mailbox.com</li>
      <li><svg viewBox="0 0 12 12"><circle cx="6" cy="6" r="5"/><path d="M1 6h10M6 1c-2.5 3-2.5 7 0 10M6 1c2.5 3 2.5 7 0 10"/></svg>www.zumparts.com</li>
      <li><svg viewBox="0 0 12 12"><circle cx="6" cy="4" r="2.2"/><path d="M2 11c.5-2.5 2-3.5 4-3.5s3.5 1 4 3.5"/></svg>reno.tam22</li>
    </ul>
    <div class="partner-brands">
      <span class="partner-peltaro">PELTARO</span>
      <span class="partner-vorn">VORN MOTORS</span>
      <span class="partner-738">738</span>
      <span class="partner-note">Genuine Parts</span>
    </div>
    <span class="back-watermark">ZUM</span>
  </section>
</body>
</html>
```